Stonebridge Building and Projects business cards

A business card with watermark background (construction work)

Company logo attached

Home improvement projects
House renovations
Bathroom and kitchen renovations
House extensions
New builds and granny flats

Director Omar Haddani
(Phone number)
omar@sbpbuilding.com.au
(Instagram logo) sbp_building

```html
<!DOCTYPE html>
<html lang="en">
<head>
<meta charset="utf-8">
<title>Stonebridge Building and Projects – Business Card</title>
<link href="https://fonts.googleapis.com/css2?family=Roboto:wght@400;500;700&family=Signika:wght@500;600&display=swap" rel="stylesheet">
<style>
  :root {
    --page-bg: #d9d6d2;
    --card-bg: #eef0f1;
    --brand-blue: #1f6fb2;
    --text-dark: #3a3d40;
    --icon-dark: #404447;
    --pattern-grey: #b9bcbf;
    --pattern-blue: #2a78b8;
  }
  * { margin: 0; padding: 0; box-sizing: border-box; }
  html, body {
    width: 1200px;
    height: 1054px;
    overflow: hidden;
    background: var(--page-bg);
  }
  .business-card {
    position: absolute;
    left: 100px;
    top: 227px;
    width: 1000px;
    height: 600px;
    background: var(--card-bg);
    border-radius: 20px;
    overflow: hidden;
    box-shadow: 0 10px 30px rgba(0,0,0,0.15);
  }
  .brand-lockup {
    position: absolute;
    left: 48px;
    top: 66px;
    display: flex;
    align-items: center;
    gap: 18px;
  }
  .brand-square {
    width: 58px;
    height: 58px;
    background: var(--brand-blue);
  }
  .brand-name {
    font-family: "Roboto", sans-serif;
    font-weight: 500;
    font-size: 30px;
    line-height: 1.15;
    color: var(--brand-blue);
  }
  .person-name {
    position: absolute;
    left: 46px;
    top: 280px;
    font-family: "Signika", sans-serif;
    font-weight: 600;
    font-size: 38px;
    color: var(--brand-blue);
  }
  .person-role {
    position: absolute;
    left: 46px;
    top: 330px;
    font-family: "Roboto", sans-serif;
    font-size: 25px;
    color: var(--text-dark);
  }
  .contact-list {
    position: absolute;
    left: 46px;
    top: 405px;
    list-style: none;
  }
  .contact-item {
    display: flex;
    align-items: center;
    gap: 16px;
    height: 38px;
    font-family: "Roboto", sans-serif;
    font-size: 25px;
    color: var(--text-dark);
  }
  .contact-icon { width: 24px; height: 24px; flex: none; }
  .decor-pattern {
    position: absolute;
    left: 590px;
    top: 40px;
    width: 410px;
    height: 560px;
    background: linear-gradient(100deg, rgba(185,188,191,0) 0%, var(--pattern-grey) 45%, var(--pattern-blue) 75%, #1d5f98 100%);
    opacity: 0.85;
  }
</style>
</head>
<body>
  <main class="business-card">
    <div class="decor-pattern" role="img" aria-label="Decorative building-block pattern in grey and blue"></div>

    <div class="brand-lockup">
      <div class="brand-square"></div>
      <div class="brand-name">Stonebridge<br>Building and Projects</div>
    </div>

    <h1 class="person-name">Omar Haddani</h1>
    <p class="person-role">Managing Director</p>

    <ul class="contact-list">
      <li class="contact-item">
        <svg class="contact-icon" viewBox="0 0 24 24" fill="none" stroke="var(--icon-dark)" stroke-width="2"><circle cx="12" cy="12" r="10"/><path d="M8.5 7.5l2 2-1 1.5a7 7 0 0 0 3.5 3.5l1.5-1 2 2-1.5 1.5c-3.5 0-8-4.5-8-8z" stroke-width="1.5"/></svg>
        <span>0400 318 726</span>
      </li>
      <li class="contact-item">
        <svg class="contact-icon" viewBox="0 0 24 24" fill="none" stroke="var(--icon-dark)" stroke-width="2"><rect x="2" y="5" width="20" height="14" rx="1"/><path d="M2 6l10 7 10-7"/></svg>
        <span>omar@sbpbuilding.com.au</span>
      </li>
      <li class="contact-item">
        <svg class="contact-icon" viewBox="0 0 24 24" fill="none" stroke="var(--icon-dark)" stroke-width="2"><circle cx="12" cy="12" r="10"/><path d="M2 12h20M12 2c3 3 3 17 0 20M12 2c-3 3-3 17 0 20"/></svg>
        <span>sbpbuilding.com.au</span>
      </li>
      <li class="contact-item">
        <svg class="contact-icon" viewBox="0 0 24 24" fill="none" stroke="var(--icon-dark)" stroke-width="2"><circle cx="12" cy="12" r="9"/></svg>
        <span>sbp_building</span>
      </li>
    </ul>
  </main>
</body>
</html>
```